Letterhead for Conveyancing Company

Use existing logo to create a letterhead for a conveyancing company. Must be able to be used in Microsoft Word. Easy to read and professional.
Contact information to be at the bottom.
Bright Oak Conveyancing Pty Ltd
ACN 621 984 736PO Box 535 Campbelltown SA 5074
Mobile - 0461739286
Web address - www.brightoakconveyancing.com.au

Requirements
Must have
• Logo and contact details.
• Simple and professional.

```html
<!DOCTYPE html>
<html lang="en">
<head>
<meta charset="utf-8">
<title>Bright Oak Conveyancing – Letterhead</title>
<link href="https://fonts.googleapis.com/css2?family=Arimo:wght@400;700&family=Tinos&display=swap" rel="stylesheet">
<style>
  :root {
    --backdrop: #d9dcdd;
    --paper: #ffffff;
    --brand-pink: #e0197d;
    --ink-grey: #6f6f6f;
    --soft-grey: #b9b9b9;
  }
  * { box-sizing: border-box; margin: 0; padding: 0; }
  html, body { width: 1200px; height: 784px; overflow: hidden; }
  body {
    background: var(--backdrop);
    display: flex;
    align-items: center;
    justify-content: center;
  }
  .letterhead {
    position: relative;
    width: 524px;
    height: 740px;
    background: var(--paper);
    box-shadow: 0 4px 18px rgba(0,0,0,0.12);
    padding: 46px 50px 40px 56px;
    font-family: "Arimo", Arial, sans-serif;
    color: var(--ink-grey);
  }
  .brand {
    display: flex;
    justify-content: flex-end;
    align-items: center;
    gap: 8px;
  }
  .brand-mark {
    width: 14px;
    height: 14px;
    background: var(--brand-pink);
  }
  .brand-name {
    font-weight: 700;
    font-size: 22px;
    line-height: 1.05;
    color: var(--brand-pink);
    text-align: right;
    letter-spacing: 0.5px;
  }
  .letter-body {
    margin-top: 22px;
    font-size: 9.4px;
    line-height: 1.5;
  }
  .letter-body p { margin-bottom: 11px; }
  .signature {
    margin-top: 8px;
    width: 150px;
    height: 42px;
    background: linear-gradient(90deg, #f1f1f1, #e6e6e6);
  }
  .contact-footer {
    position: absolute;
    left: 56px;
    right: 50px;
    bottom: 40px;
    font-family: "Tinos", "Times New Roman", serif;
  }
  .company-name {
    color: var(--brand-pink);
    font-size: 12px;
    font-variant: small-caps;
    letter-spacing: 0.6px;
    padding-bottom: 6px;
    border-bottom: 1px solid var(--soft-grey);
    width: 230px;
  }
  .contact-columns {
    display: flex;
    margin-top: 8px;
    font-size: 8.6px;
    color: var(--ink-grey);
  }
  .contact-column { display: flex; flex-direction: column; gap: 4px; }
  .contact-column.primary { padding-right: 22px; border-right: 1px solid var(--soft-grey); }
  .contact-column.secondary { padding-left: 16px; }
  .contact-line { display: flex; align-items: center; gap: 6px; }
  .contact-line.indent { padding-left: 15px; }
  .contact-icon { width: 9px; height: 9px; flex: none; }
</style>
</head>
<body>
  <main class="letterhead">
    <header class="brand">
      <span class="brand-mark"></span>
      <div class="brand-name">Bright Oak<br>Conveyancing</div>
    </header>

    <section class="letter-body">
      <p>Lorem Ipsum is simply dummy text of the printing and typesetting industry. Lorem Ipsum has been the industry's standard dummy text ever since the 1500s, when an unknown printer took a galley of type and scrambled it to make a type specimen book. It has survived not only five centuries, but also the leap into electronic typesetting, remaining essentially unchanged. It was popularised in the 1960s with the release of Typeline sheets containing Lorem Ipsum passages, and more recently with desktop publishing software like Quillset Layout including versions of Lorem Ipsum.</p>
      <p>It is a long established fact that a reader will be distracted by the readable content of a page when looking at its layout. The point of using Lorem Ipsum is that it has a more-or-less normal distribution of letters, as opposed to using 'Content here, content here', making it look like readable English. Many desktop publishing packages and web page editors now use Lorem Ipsum as their default model text, and a search for 'lorem ipsum' will uncover many web sites still in their infancy. Various versions have evolved over the years, sometimes by accident, sometimes on purpose (injected humour and the like).</p>
      <p>Contrary to popular belief, Lorem Ipsum is not simply random text. It has roots in a piece of classical Latin literature from 45 BC, making it over 2000 years old. Edwin Marsh, a Latin professor at Harlow Ridge College in Virginia, looked up one of the more obscure Latin words, consectetur, from a Lorem Ipsum passage, and going through the cites of the word in classical literature, discovered the undoubtable source. Lorem Ipsum comes from sections 1.10.32 and 1.10.33 of "de Finibus Bonorum et Malorum" structures, to generate Lorem Ipsum which looks reasonable. The generated Lorem Ipsum is therefore always free from repetition, injected humour, or non-characteristic words etc.</p>
      <div class="signature" role="img" aria-label="Handwritten signature of the sender"></div>
    </section>

    <footer class="contact-footer">
      <div class="company-name">Bright Oak Conveyancing Pty Ltd</div>
      <div class="contact-columns">
        <div class="contact-column primary">
          <div class="contact-line">
            <svg class="contact-icon" viewBox="0 0 10 10" aria-hidden="true"><circle cx="5" cy="5" r="5" fill="#e0197d"/><path d="M5 2.2a1.7 1.7 0 0 0-1.7 1.7C3.3 5.2 5 7.6 5 7.6s1.7-2.4 1.7-3.7A1.7 1.7 0 0 0 5 2.2z" fill="#fff"/></svg>
            <span>PO Box 871 Marlowdale</span>
          </div>
          <div class="contact-line indent">SA 5096</div>
          <div class="contact-line">
            <svg class="contact-icon" viewBox="0 0 10 10" aria-hidden="true"><circle cx="5" cy="5" r="5" fill="#e0197d"/><rect x="3" y="3" width="4" height="4" fill="#fff"/></svg>
            <span>ACN 583 217 469</span>
          </div>
        </div>
        <div class="contact-column secondary">
          <div class="contact-line">
            <svg class="contact-icon" viewBox="0 0 10 10" aria-hidden="true"><circle cx="5" cy="5" r="5" fill="#e0197d"/><rect x="3.6" y="2" width="2.8" height="6" rx="0.6" fill="#fff"/></svg>
            <span>0461739286</span>
          </div>
          <div class="contact-line">
            <svg class="contact-icon" viewBox="0 0 10 10" aria-hidden="true"><circle cx="5" cy="5" r="5" fill="#e0197d"/><rect x="2.4" y="3.2" width="5.2" height="3.6" fill="#fff"/><path d="M2.4 3.2 5 5.2l2.6-2" stroke="#e0197d" stroke-width="0.6" fill="none"/></svg>
            <span>contact@brightoakconveyancing.com.au</span>
          </div>
          <div class="contact-line">
            <svg class="contact-icon" viewBox="0 0 10 10" aria-hidden="true"><circle cx="5" cy="5" r="5" fill="#e0197d"/><circle cx="5" cy="5" r="2.6" fill="none" stroke="#fff" stroke-width="0.7"/><path d="M2.4 5h5.2M5 2.4v5.2" stroke="#fff" stroke-width="0.6"/></svg>
            <span>www.brightoakconveyancing.com.au</span>
          </div>
        </div>
      </div>
    </footer>
  </main>
</body>
</html>
```